Business Card Design - Amberfield Court

We are looking at a new design for our business cards that has a modern and professional look. We run a residential aged care facility focussing on the care of residents. The cards will be used for potential clients, consultants and business opportunities in this sector. Blue and white is our main colours and would to see these colours incorporated in the design.
Industry/Entity Type
Business
Contact Information for Business Card
Amberfield Court, Darren Walsh, dwalsh@amberfieldcourt.com.au, Finance Manager, 0472 639 208, BCom, 37 Marrabel Crescent, Brindle Vale, Qld 4093.
Look and feel
Each slider illustrates characteristics of the customer's brand and the style your logo design should communicate.

```html
<!DOCTYPE html>
<html lang="en">
<head>
<meta charset="utf-8">
<title>Amberfield Court – Business Cards</title>
<link href="https://fonts.googleapis.com/css2?family=Open+Sans:wght@400;600;700&display=swap" rel="stylesheet">
<style>
  :root {
    --backdrop: #e6e8ea;
    --card-white: #ffffff;
    --navy: #1f3a4a;
    --brand-blue: #4b7d99;
    --text-light: #ffffff;
  }
  * { margin: 0; padding: 0; box-sizing: border-box; }
  html, body { width: 1200px; height: 900px; overflow: hidden; }
  body {
    background: var(--backdrop);
    font-family: "Open Sans", Arial, sans-serif;
    position: relative;
  }
  .card {
    position: absolute;
    width: 620px;
    height: 380px;
    background: var(--card-white);
    border-radius: 22px;
    overflow: hidden;
    box-shadow: 0 6px 18px rgba(0,0,0,0.15);
  }
  .card-front { left: 290px; top: 50px; }
  .card-back { left: 290px; top: 470px; }

  .brand {
    display: flex;
    align-items: center;
    gap: 14px;
    color: var(--navy);
    font-weight: 600;
    white-space: nowrap;
  }
  .brand-dot {
    border-radius: 50%;
    background: var(--brand-blue);
    flex: none;
  }
  .card-front .brand {
    position: absolute;
    left: 50%; top: 50%;
    transform: translate(-50%, -50%);
    font-size: 40px;
  }
  .card-front .brand-dot { width: 58px; height: 58px; }

  .back-panel { position: absolute; inset: 0; }
  .card-back .brand {
    position: absolute;
    right: 40px; top: 92px;
    font-size: 24px;
    gap: 10px;
  }
  .card-back .brand-dot { width: 36px; height: 36px; }

  .contact {
    position: absolute;
    left: 58px; top: 150px;
    color: var(--text-light);
  }
  .contact-name {
    font-size: 30px;
    font-weight: 700;
    letter-spacing: 0.5px;
    line-height: 1.1;
  }
  .contact-role {
    font-size: 14px;
    font-weight: 400;
    letter-spacing: 0.4px;
    margin-bottom: 18px;
  }
  .contact-address { font-size: 15px; line-height: 1.35; margin-bottom: 14px; }
  .contact-line {
    display: flex; align-items: center; gap: 8px;
    font-size: 15px; line-height: 1.5;
  }
  .contact-line svg { width: 13px; height: 13px; flex: none; }
</style>
</head>
<body>

  <section class="card card-front">
    <div class="brand">
      <span class="brand-dot"></span>
      <span class="brand-name">Amberfield Court</span>
    </div>
  </section>

  <section class="card card-back">
    <svg class="back-panel" viewBox="0 0 620 380" width="620" height="380" aria-hidden="true">
      <circle cx="-60" cy="420" r="452" fill="none" stroke="var(--brand-blue)" stroke-width="4"/>
      <circle cx="-60" cy="420" r="440" fill="var(--navy)"/>
    </svg>

    <div class="brand">
      <span class="brand-dot"></span>
      <span class="brand-name">Amberfield Court</span>
    </div>

    <div class="contact">
      <p class="contact-name">DARREN WALSH</p>
      <p class="contact-role">FINANCE MANAGER (BCOM)</p>
      <p class="contact-address">37 Marrabel Crescent<br>Brindle Vale, Qld 4093</p>
      <p class="contact-line">
        <svg viewBox="0 0 24 24" fill="currentColor"><path d="M6.6 10.8a15.1 15.1 0 0 0 6.6 6.6l2.2-2.2a1 1 0 0 1 1-.25 11.4 11.4 0 0 0 3.6.57 1 1 0 0 1 1 1V20a1 1 0 0 1-1 1A17 17 0 0 1 3 4a1 1 0 0 1 1-1h3.5a1 1 0 0 1 1 1c0 1.25.2 2.45.57 3.6a1 1 0 0 1-.25 1z"/></svg>
        0472 639 208
      </p>
      <p class="contact-line">
        <svg viewBox="0 0 24 24" fill="none" stroke="currentColor" stroke-width="2.4"><rect x="2" y="5" width="20" height="14" rx="1"/><path d="M2 6l10 7 10-7"/></svg>
        dwalsh@amberfieldcourt.com.au
      </p>
    </div>
  </section>

</body>
</html>
```